Business Card Design

My business is writing crime novels to entertain readers. I write legal thrillers and mysteries. I need a card for publishers, agents, other authors, and media.

Industry/Entity Type

Legal

Contact Information for Business Card

Paul Derrow
www.derrowfiction.example
pauljderrow@inkpost.example
0064 27 5190472

```html
<!DOCTYPE html>
<html lang="en">
<head>
<meta charset="utf-8">
<title>Paul Derrow – Business Card</title>
<link rel="stylesheet" href="https://fonts.googleapis.com/css2?family=Gochi+Hand&family=Cabin:wght@400&display=swap">
<style>
  :root {
    --page-bg: #e9e2d2;
    --card-black: #050505;
    --smoke-red: #5a0608;
    --band-red: #d40000;
    --band-red-dark: #8e0000;
    --stripe-white: #ffffff;
    --text-white: #ffffff;
    --text-soft: #e8e8e8;
    --portrait-light: #6a6a6a;
    --portrait-dark: #1b1b1b;
  }
  html, body {
    margin: 0;
    padding: 0;
    width: 1200px;
    height: 729px;
    overflow: hidden;
    background: var(--page-bg);
  }
  .canvas {
    position: relative;
    width: 1200px;
    height: 729px;
  }
  .business-card {
    position: absolute;
    left: 150px;
    top: 107px;
    width: 900px;
    height: 514px;
    filter: drop-shadow(0 8px 18px rgba(0,0,0,0.35));
  }
  .card-name {
    font-family: "Gochi Hand", cursive;
    font-size: 52px;
    fill: var(--text-white);
    letter-spacing: 1px;
  }
  .card-contact {
    font-family: "Cabin", sans-serif;
    font-size: 22px;
    fill: var(--text-soft);
  }
  .card-web {
    font-family: "Cabin", sans-serif;
    font-size: 22px;
    fill: var(--text-white);
    letter-spacing: 1.5px;
  }
</style>
</head>
<body>
<main class="canvas">
  <svg class="business-card" viewBox="0 0 900 514" xmlns="http://www.w3.org/2000/svg">
    <defs>
      <clipPath id="card-shape">
        <rect width="900" height="514" rx="26" ry="26"/>
      </clipPath>
      <radialGradient id="smoke-glow" cx="0.55" cy="0.4" r="0.6">
        <stop offset="0" stop-color="var(--smoke-red)" stop-opacity="0.85"/>
        <stop offset="0.6" stop-color="var(--smoke-red)" stop-opacity="0.35"/>
        <stop offset="1" stop-color="var(--card-black)" stop-opacity="0"/>
      </radialGradient>
      <linearGradient id="portrait-tone" x1="0" y1="0" x2="0" y2="1">
        <stop offset="0" stop-color="var(--portrait-light)"/>
        <stop offset="1" stop-color="var(--portrait-dark)"/>
      </linearGradient>
      <linearGradient id="band-tone" x1="0" y1="0" x2="0" y2="1">
        <stop offset="0" stop-color="var(--band-red)"/>
        <stop offset="1" stop-color="var(--band-red-dark)"/>
      </linearGradient>
    </defs>

    <g clip-path="url(#card-shape)">
      <rect class="card-base" width="900" height="514" fill="var(--card-black)"/>
      <rect class="smoke-texture" x="0" y="0" width="640" height="480" fill="url(#smoke-glow)"
            role="img" aria-label="Dark red smoke wisps drifting across the black background"/>
      <rect class="author-portrait" x="580" y="20" width="320" height="380" fill="url(#portrait-tone)"
            role="img" aria-label="Portrait photo of the author in glasses, white shirt and black leather jacket"/>
      <polygon class="white-stripe" points="0,438 540,438 512,474 0,474" fill="var(--stripe-white)"/>
      <polygon class="red-band" points="0,482 520,482 568,396 900,396 900,514 0,514" fill="url(#band-tone)"/>
    </g>

    <text class="card-name" x="120" y="318">Paul Derrow</text>
    <text class="card-contact" x="250" y="365" text-anchor="middle">0064 27 5190472</text>
    <text class="card-contact" x="250" y="400" text-anchor="middle">pauljderrow@inkpost.example</text>
    <text class="card-web" x="878" y="442" text-anchor="end">www.derrowfiction.example</text>
  </svg>
</main>
</body>
</html>
```